ReelBloom business card

We are a performing arts company providing training (to both kids and adults) as well as performers for events. We hope to bring joy and confidence on stage to the people we train, as well as joy to the audience when our artistes perform. Designs should convey the joy, confidence and vibrancy on stage. Design business card using the attached logo. Card to include name, mobile tel, email address, company address, and website. Double sided. To also include the following list of what the company does:
• Training & Enrichment
• Private & Corporate Entertainment
- Music composition & production

Industry/Entity Type

Training

Contact Information for Business Card

Card to include name, mobile tel, email address, company address, and website. Double sided. To also include the following list of what the company does:
• Training & Enrichment

Requirements
Nice to have
• Card need not be the traditional rectangular in shape but not too outrageous.

```html
<!DOCTYPE html>
<html lang="en">
<head>
<meta charset="utf-8">
<title>ReelBloom business card</title>
<link rel="stylesheet" href="https://fonts.googleapis.com/css2?family=Montserrat:wght@400;600&display=swap">
<style>
  :root {
    --bg: #e7e3dd;
    --card: #f7f7f8;
    --card-edge: #e2e2e6;
    --navy: #232466;
    --ink: #1d1d22;
    --muted: #3a3a44;
    --brand: #3a2f9a;
    --figure-a: #b9b6d6;
    --figure-b: #f1d8c2;
  }
  * { box-sizing: border-box; margin: 0; padding: 0; }
  html, body { width: 1200px; height: 885px; overflow: hidden; }
  body {
    background: var(--bg);
    font-family: "Montserrat", Arial, sans-serif;
    position: relative;
  }
  .card {
    position: absolute;
    background: linear-gradient(160deg, #ffffff 0%, var(--card) 60%, var(--card-edge) 100%);
    border-radius: 22px;
    box-shadow: 0 10px 30px rgba(60, 50, 40, 0.25);
    overflow: hidden;
  }
  /* Front */
  .card-front {
    left: 50px; top: 272px; width: 580px; height: 340px;
    display: flex; flex-direction: column; align-items: center; justify-content: center;
    text-align: center;
  }
  .brand-name {
    font-family: "Montserrat", Arial, sans-serif;
    font-weight: 600;
    color: var(--brand);
    font-size: 76px;
    line-height: 1;
  }
  .tagline {
    color: var(--navy);
    font-size: 24px;
    margin-top: 12px;
  }
  .services {
    margin-top: 24px;
    font-size: 13px;
    color: var(--muted);
    line-height: 1.55;
  }
  /* Back */
  .card-back {
    left: 790px; top: 150px; width: 340px; height: 585px;
  }
  .back-figures {
    position: absolute;
    right: 0; top: 250px; width: 210px; height: 240px;
    background: radial-gradient(ellipse at 55% 45%, var(--figure-a) 0%, rgba(241,216,194,0.55) 55%, rgba(255,255,255,0) 80%);
    opacity: 0.55;
  }
  .back-content {
    position: relative;
    display: flex; flex-direction: column; align-items: center;
    text-align: center;
    padding-top: 84px;
  }
  .back-brand {
    font-family: "Montserrat", Arial, sans-serif;
    font-weight: 600;
    color: var(--brand);
    font-size: 44px;
    line-height: 1;
  }
  .back-tagline {
    color: var(--navy);
    font-size: 15px;
    margin-top: 8px;
  }
  .person { margin-top: 54px; }
  .person-name { font-weight: 600; font-size: 21px; color: var(--ink); letter-spacing: 0.5px; }
  .person-title { font-size: 15px; color: var(--ink); }
  .contact {
    margin-top: 68px;
    font-size: 15px;
    color: var(--ink);
    line-height: 1.45;
    list-style: none;
  }
  .web-band {
    position: absolute;
    left: 0; right: 0; bottom: 0; height: 64px;
    background: var(--navy);
    color: #ffffff;
    display: flex; align-items: center; justify-content: center;
    font-size: 21px;
    letter-spacing: 0.8px;
  }
</style>
</head>
<body>
  <section class="card card-front">
    <h1 class="brand-name">ReelBloom</h1>
    <p class="tagline">where talent takes the stage</p>
    <p class="services">Coaching &amp; Workshops | Event &amp; Corporate Shows<br>Original scoring &amp; recording</p>
  </section>

  <section class="card card-back">
    <div class="back-figures" role="img" aria-label="Faint illustration of joyful dancing performers with music notes"></div>
    <div class="back-content">
      <h2 class="back-brand">ReelBloom</h2>
      <p class="back-tagline">where talent takes the stage</p>
      <div class="person">
        <p class="person-name">Employee Name</p>
        <p class="person-title">Your Title</p>
      </div>
      <ul class="contact">
        <li>0045 7812 360</li>
        <li>hello@reelbloomarts.com</li>
        <li>18 Larkspur Row Studio 4</li>
        <li>NJ 07311</li>
      </ul>
    </div>
    <div class="web-band">www.reelbloomarts.com</div>
  </section>
</body>
</html>
```